Unique Business Card Design

Unique Business Card design for our orthotic and prosthetic company. Our logo is on our website, color is light blue. Unique shape (artificial leg shaped, vertical, etc..) preferred. Logo, business name, individual name and basic demographics needed.

Industry/Entity Type

Business

Contact Information for Business Card

Logo, Industry, Phone # Logo, "Prosthetic & Orthotic Services" Place to add individual name and contact info

Colors
cee9f5

Requirements
Must have
• The icon must be there, placement of "Prosthetic & Orthotic Services" can be moved
Nice to have
• Like the mix of light blue, and a little darker blue. One design included the icons from my website which was a nice touch

```html
<!DOCTYPE html>
<html lang="en">
<head>
<meta charset="utf-8">
<title>Limbwell Inc. – Business Cards</title>
<link rel="stylesheet" href="https://fonts.googleapis.com/css2?family=Open+Sans:wght@400;600;700&family=Arimo:wght@700&family=Crimson+Text:ital@1&display=swap">
<style>
  :root {
    --bg: #1c1c1e;
    --blue-deep: #1b64b8;
    --blue-mid: #2382c8;
    --blue-brand: #1f6fc0;
    --white: #ffffff;
    --white-soft: rgba(255,255,255,0.82);
  }
  * { box-sizing: border-box; margin: 0; padding: 0; }
  html, body { width: 1200px; height: 1000px; overflow: hidden; }
  body {
    background: var(--bg);
    font-family: "Open Sans", Arial, sans-serif;
    position: relative;
  }
  .card {
    position: absolute;
    left: 250px;
    width: 700px;
    height: 400px;
    border-radius: 40px;
    overflow: hidden;
  }
  .card--front {
    top: 60px;
    background: linear-gradient(135deg, var(--blue-deep) 0%, var(--blue-mid) 60%, var(--blue-deep) 100%);
    color: var(--white);
  }
  .card--back { top: 540px; background: var(--white); }
  .card__shape { position: absolute; inset: 0; }

  .brand { position: absolute; text-align: center; }
  .brand__mark {
    display: block; width: 74px; height: 74px; border-radius: 50%;
    margin: 0 auto 6px;
  }
  .brand__name {
    font-family: "Open Sans", Arial, sans-serif;
    font-weight: 600; font-size: 34px; letter-spacing: 0.5px; line-height: 1;
    padding-bottom: 6px; border-bottom: 2px solid currentColor;
  }
  .brand__tagline {
    font-family: "Crimson Text", Georgia, serif;
    font-style: italic; font-size: 20px; margin-top: 4px;
  }
  .brand__phone {
    font-family: "Arimo", Arial, sans-serif;
    font-weight: 700; font-size: 40px; margin-top: 12px; letter-spacing: 0.5px;
  }

  .card--front .brand { left: 0; right: 0; top: 70px; }
  .card--front .brand__inner { display: inline-block; }
  .card--front .brand__mark { background: var(--white); }
  .web-line {
    position: absolute; left: 0; right: 0; top: 320px;
    text-align: center; font-size: 19px; color: var(--white-soft);
    display: flex; justify-content: center; align-items: center; gap: 8px;
  }

  .card--back .brand { left: 40px; top: 110px; color: var(--blue-brand); }
  .card--back .brand__mark { background: var(--blue-brand); }
  .card--back .brand__phone { font-size: 42px; }

  .person {
    position: absolute; left: 445px; top: 62px; color: var(--white);
  }
  .person__name { font-weight: 700; font-size: 27px; line-height: 1.1; }
  .person__title { font-weight: 600; font-size: 19px; margin-bottom: 14px; }
  .person__address { font-size: 16px; color: var(--white-soft); line-height: 1.3; margin-bottom: 14px; }
  .contact { list-style: none; font-size: 16px; color: var(--white-soft); }
  .contact li { display: flex; align-items: center; gap: 10px; line-height: 1.5; }
  .contact svg { width: 14px; height: 14px; flex: none; }
</style>
</head>
<body>

<section class="card card--front" aria-label="Business card front">
  <div class="brand">
    <div class="brand__inner">
      <span class="brand__mark"></span>
      <div class="brand__name">LIMBWELL INC.</div>
      <div class="brand__tagline">Prosthetic &amp; Orthotic Services</div>
      <div class="brand__phone">718.555.0142</div>
    </div>
  </div>
  <div class="web-line">
    <svg width="16" height="16" viewBox="0 0 16 16" fill="none" stroke="currentColor" stroke-width="1.4"><circle cx="8" cy="8" r="6.5"/><ellipse cx="8" cy="8" rx="3" ry="6.5"/><line x1="1.5" y1="8" x2="14.5" y2="8"/></svg>
    <span>yoursitename.com</span>
  </div>
</section>

<section class="card card--back" aria-label="Business card back">
  <svg class="card__shape" viewBox="0 0 700 400" preserveAspectRatio="none" aria-hidden="true">
    <defs>
      <linearGradient id="panelBlue" x1="0" y1="0" x2="1" y2="1">
        <stop offset="0" stop-color="#1b64b8"/>
        <stop offset="0.6" stop-color="#2382c8"/>
        <stop offset="1" stop-color="#1b64b8"/>
      </linearGradient>
    </defs>
    <path d="M300 0 Q 470 150 400 400 L 700 400 L 700 0 Z" fill="url(#panelBlue)"/>
    <path d="M328 0 Q 498 150 428 400" fill="none" stroke="#ffffff" stroke-width="7"/>
  </svg>

  <div class="brand">
    <div class="brand__inner">
      <span class="brand__mark"></span>
      <div class="brand__name">LIMBWELL INC.</div>
      <div class="brand__tagline">Prosthetic &amp; Orthotic Services</div>
      <div class="brand__phone">718.555.0142</div>
    </div>
  </div>

  <div class="person">
    <div class="person__name">DANA WHITFIELD</div>
    <div class="person__title">Director</div>
    <div class="person__address">Your Street Address,<br>New York, 1234</div>
    <ul class="contact">
      <li><svg viewBox="0 0 16 16" fill="currentColor"><path d="M3.5 1.5l2.5 0 1 3.5-1.6 1.2a8 8 0 0 0 4.4 4.4L11 9l3.5 1v2.5A1.8 1.8 0 0 1 12.7 14 11 11 0 0 1 2 3.3 1.8 1.8 0 0 1 3.5 1.5z"/></svg>+000 12345 6789</li>
      <li><svg viewBox="0 0 16 16" fill="none" stroke="currentColor" stroke-width="1.4"><rect x="1.5" y="3.5" width="13" height="9"/><path d="M1.5 3.5l6.5 5 6.5-5"/></svg>yourname@email.com</li>
      <li><svg viewBox="0 0 16 16" fill="none" stroke="currentColor" stroke-width="1.4"><circle cx="8" cy="8" r="6.5"/><ellipse cx="8" cy="8" rx="3" ry="6.5"/><line x1="1.5" y1="8" x2="14.5" y2="8"/></svg>www.yoursitename.com</li>
    </ul>
  </div>
</section>

</body>
</html>
```